Useable Postcard Gift for Artistic Convention Use

Useable Postcard Gift Conference Use, search for web designers
Name of the Company is: Verdancy Harbor
I have an image that I would like to use for the front of the card
along with a by line which says "Let Each Step Light the Road Ahead"
Regarding image, i am good to leave the black behind.... should the designer choose. I also have a black and white image to use as well if someone needs it.

Design Target Market: State of the Art, Hip, Elegant, Conscious

This card will be used at a state of the art tech Quorvel Summit in Los Angeles. We want to hand it out to those we are interested in continuing relationship with for the purpose of building a website that is comprehensive. We are looking for designers and tech builders for the site.

This is a service business. I would like to have 3 names and titles on the back of the card and a small paragraph of copy. I like the beauty of the postcard i have saved on my account. I like Copper Gothic, thin lettering and Amazone or Caligraphy where it fits.... if it fits.

I want the card to communicate interest in Verdancy Harbor as a state of the art web community that services those progressive professionals who are interested in personal balance and who want to purchase products that are essential to a healthful life.
Updates

Project Deadline Extended
Reason: The deadline is extended through tomorrow due to the need to complete a design. Please continue support

Target Market(s)

High profile clients for coaching, web designers and web technicians for elaborate website build.

Industry/Entity Type

Progressive

Font styles to use
Serif
Script

Colors
00a88f
0555a3
6b449b
ffc214
9bcb3b
f37022

Requirements
Nice to have
• This was supposed to be the must have feature but it wouldn't return there so-----
We want the card to be elegant and definitely a useable postcard.

```html
<!DOCTYPE html>
<html lang="en">
<head>
<meta charset="utf-8">
<title>Verdancy Harbor – Postcard Back</title>
<link rel="stylesheet" href="https://fonts.googleapis.com/css2?family=Cinzel:wght@400&family=Italianno&family=Jost:wght@400&display=swap">
<style>
  :root {
    --orange: #ff8c00;
    --ink: #000000;
    --violet: #5b2ee6;
    --violet-deep: #4a1fd6;
    --callout: #ff8a00;
    --grey: #8a8a8a;
    --grey-text: #6e6e6e;
    --paper: #ffffff;
  }
  html, body { margin: 0; padding: 0; overflow: hidden; background: var(--paper); }
  .postcard { position: relative; width: 1200px; height: 930px; background: var(--paper); overflow: hidden; }

  .title-band {
    position: absolute; left: 0; top: 0; width: 569px; height: 78px;
    background: var(--orange);
    display: flex; align-items: flex-end; justify-content: center;
  }
  .title-band h1 {
    margin: 0 0 6px 10px; font-family: "Cinzel", serif; font-weight: 400;
    font-size: 40px; color: var(--paper); letter-spacing: 1px; line-height: 1;
  }
  .title-rule { position: absolute; left: 0; top: 82px; width: 569px; height: 3px; background: var(--ink); }
  .divider { position: absolute; left: 573px; top: 0; width: 5px; height: 766px; background: var(--ink); }

  .pitch {
    position: absolute; left: 36px; top: 98px; width: 509px;
    font-family: "Italianno", cursive; font-size: 33px; line-height: 37.5px;
    color: var(--violet); text-align: justify;
  }
  .pitch p { margin: 0; text-indent: 46px; }

  .callout {
    position: absolute; left: 75px; top: 517px; width: 439px; height: 66px;
    border-top: 2px solid var(--ink); border-bottom: 2px solid var(--ink);
    font-family: "Jost", sans-serif; font-size: 22px; line-height: 31px;
    color: var(--callout); text-align: center; padding-top: 2px; box-sizing: content-box;
  }

  .team { position: absolute; left: 38px; top: 596px; margin: 0; padding: 0; list-style: none; font-family: "Jost", sans-serif; color: var(--violet-deep); }
  .member { position: relative; padding-left: 22px; height: 102px; }
  .member::before { content: ""; position: absolute; left: 2px; top: 14px; width: 9px; height: 9px; border-radius: 50%; background: var(--violet-deep); }
  .member-name { display: block; font-size: 25px; line-height: 32px; }
  .member-role, .member-phone { display: block; font-size: 21px; line-height: 28px; }

  .postage {
    position: absolute; left: 967px; top: 88px; width: 134px; height: 133px;
    border: 2px solid var(--grey); box-sizing: border-box;
    display: flex; align-items: center; justify-content: center; text-align: center;
    font-family: Arial, Helvetica, sans-serif; font-size: 22px; line-height: 27px; color: var(--grey-text);
  }
  .address-line { position: absolute; left: 693px; width: 397px; height: 2px; background: var(--grey); }
</style>
</head>
<body>
<main class="postcard">
  <header class="title-band"><h1>Verdancy Harbor</h1></header>
  <div class="title-rule"></div>
  <div class="divider"></div>

  <section class="pitch">
    <p>We are looking for website development, design and technical support in the Personal Life Enhancement industry.</p>
    <p>We are creating a state of the art website that enables personal development tracking, education, coaching, classes, skill building, creativity, privacy for journal and life records, a personal library and a store. The site will have capabilities linking to other sites and services to Verdancy Harbor that support our service platform.</p>
  </section>

  <div class="callout">Call us to be part of something unique<br>where excellence is a proven standard.</div>

  <ul class="team">
    <li class="member"><span class="member-name">Selene Marrowby</span><span class="member-role">Executive Director Mentor/Coach for Creatives</span><span class="member-phone">360-555-0141</span></li>
    <li class="member"><span class="member-name">Dario Ventrelli</span><span class="member-role">Operations Director, Coach Trainer</span><span class="member-phone">360-555-0178</span></li>
    <li class="member"><span class="member-name">Ken Hoshida</span><span class="member-role">Operations Assistant</span><span class="member-phone">360-555-0126</span></li>
  </ul>

  <div class="postage">Postage<br>Area</div>
  <div class="address-line" style="top:445px"></div>
  <div class="address-line" style="top:515px"></div>
  <div class="address-line" style="top:583px"></div>
  <div class="address-line" style="top:652px"></div>
</main>
</body>
</html>
```